Brightmill Data Works

Our company is about IT hardwares and IT solutions. IT hardware such as PC, RAMS, storage and servers. IT solutions such as project management, BA. We are also selling new technology too.

Target Market(s)

Consumer, Small to Medium Business, Corporate

Requirements
Must have
• The business card must have the following:
• Name:
• Title:
• Contact Number:
• Email address:
• Website:
• Color: Must match the logo color upgrade

```html
<!DOCTYPE html>
<html lang="en">
<head>
<meta charset="utf-8">
<title>Brightmill Data Works – Business Card</title>
<link href="https://fonts.googleapis.com/css2?family=Saira+Semi+Condensed:wght@500;700&family=Roboto:wght@400&display=swap" rel="stylesheet">
<style>
  :root {
    --backdrop: #e3e3e3;
    --card-light: #f6f6f4;
    --card-dark: #1b1c1d;
    --ink: #474747;
    --ink-soft: #555555;
    --orange: #cf7a2e;
    --white: #eeeeee;
  }
  * { margin: 0; padding: 0; box-sizing: border-box; }
  html, body { width: 1200px; height: 960px; overflow: hidden; }
  body {
    background: var(--backdrop);
    position: relative;
    font-family: "Roboto", Arial, sans-serif;
  }
  .card {
    position: absolute;
    width: 600px;
    height: 343px;
    box-shadow: 0 2px 4px rgba(0,0,0,0.25);
  }
  .card-front { left: 314px; top: 113px; background: var(--card-light); }
  .card-back  { left: 311px; top: 472px; background: var(--card-dark); }

  .person { position: absolute; left: 48px; top: 178px; }
  .person-name {
    font-family: "Saira Semi Condensed", "Arial Narrow", sans-serif;
    font-weight: 500;
    font-size: 28px;
    line-height: 30px;
    color: var(--ink);
  }
  .person-title {
    font-family: "Saira Semi Condensed", "Arial Narrow", sans-serif;
    font-weight: 500;
    font-size: 15px;
    line-height: 18px;
    color: var(--orange);
  }
  .contact-list { position: absolute; left: 49px; top: 248px; list-style: none; }
  .contact-item {
    display: flex; align-items: center; gap: 6px;
    font-size: 14.5px; line-height: 19.5px; color: var(--ink-soft);
  }
  .contact-icon { width: 13px; height: 13px; fill: var(--ink); }

  .brand-mark-square { background: var(--orange); }
  .card-front .brand-mark-square {
    position: absolute; left: 360px; top: 100px;
    width: 120px; height: 120px;
  }

  .brand-back {
    position: absolute; left: 0; right: 0; top: 100px;
    display: flex; flex-direction: column; align-items: center; gap: 22px;
  }
  .card-back .brand-mark-square { width: 56px; height: 56px; }
  .brand-back-name {
    font-family: "Saira Semi Condensed", "Arial Narrow", sans-serif;
    font-weight: 700;
    font-size: 34px;
    line-height: 38px;
    color: var(--white);
  }
</style>
</head>
<body>
  <section class="card card-front">
    <div class="brand-mark-square"></div>
    <div class="person">
      <div class="person-name">DANIEL REYES</div>
      <div class="person-title">CEO/FOUNDER</div>
    </div>
    <ul class="contact-list">
      <li class="contact-item">
        <svg class="contact-icon" viewBox="0 0 16 16"><path d="M3.6 1.2l2.3 2.4c.4.4.4 1 0 1.4L4.8 6.1c.8 2 2.9 4.1 4.9 4.9l1.1-1.1c.4-.4 1-.4 1.4 0l2.4 2.3c.4.4.4 1 0 1.4l-1.3 1.3c-.6.6-1.6.8-2.4.4C6.4 13.6 2.4 9.6.7 5.1.4 4.3.6 3.3 1.2 2.7L2.2 1.2c.4-.4 1-.4 1.4 0z"/></svg>
        <span>689 555 0142</span>
      </li>
      <li class="contact-item">
        <svg class="contact-icon" viewBox="0 0 16 16"><path d="M1 3h14v1.2L8 8.6 1 4.2z"/><path d="M1 5.6l7 4.4 7-4.4V13H1z"/></svg>
        <span>daniel@brightmilldata.com</span>
      </li>
      <li class="contact-item">
        <svg class="contact-icon" viewBox="0 0 16 16"><circle cx="8" cy="8" r="7"/><path d="M5 4.5c1 .3 1.5 1.2 1 2s.3 1.5 1.2 1.5.8 1.6 0 2.4L6.6 12M11 3.8c-.6.8-.3 1.7.6 2 .9.3 1.8 0 2.2.8" stroke="#f6f6f4" stroke-width="1.3" fill="none"/></svg>
        <span>www.brightmilldata.com</span>
      </li>
    </ul>
  </section>

  <section class="card card-back">
    <div class="brand-back">
      <div class="brand-mark-square"></div>
      <div class="brand-back-name">BRIGHTMILL DATA WORKS</div>
    </div>
  </section>
</body>
</html>
```